Web Developer Needs a Business Card Design

I need a personal business card design that represents me as a web developer for potential employers. I would like the background to be a dark color on the front for contrast with my logo and name. The back will have all my information along with a smaller version of the logo. I want something with a modern look and feel, not too conservative. This will be used for potential employers and freelance work.

Industry/Entity Type

Business

Contact Information for Business Card

Front should have my logo and name. The back should have all my personal information which would include: name: Tom Varulek, phone: 570-614-3098, email: tomvarulek@quillbox.net, website url: www.tomvarulek.net, logo, web developer.

Font styles to use
Sans Serif

Requirements
Must have
• Must include my logo. The color palette base color will be the logo color.

```html
<!DOCTYPE html>
<html lang="en">
<head>
<meta charset="utf-8">
<title>Tom Varulek — Business Card</title>
<link rel="stylesheet" href="https://fonts.googleapis.com/css2?family=Arimo:wght@400;700&display=swap">
<style>
  :root {
    --ink: #000000;
    --teal: #66c6b3;
    --paper: #ffffff;
    --backdrop: #e4e4e4;
    --text-dark: #111111;
  }
  * { margin: 0; padding: 0; box-sizing: border-box; }
  html, body { width: 1189px; height: 1200px; overflow: hidden; }
  body {
    position: relative;
    background: var(--backdrop);
    font-family: "Arimo", Arial, sans-serif;
  }
  .card {
    position: absolute;
    left: 140px;
    width: 918px;
    height: 522px;
    background: var(--ink);
    overflow: hidden;
    box-shadow: 4px 6px 10px rgba(0,0,0,0.35);
  }
  .card--info { top: 47px; }
  .card--brand { top: 624px; }

  .mark {
    position: absolute;
    border-radius: 50%;
    border-style: solid;
    border-color: var(--teal);
    display: flex;
    align-items: center;
    justify-content: center;
    color: var(--teal);
    font-weight: 700;
  }
  .card--info .mark {
    left: 337px; top: 31px; width: 244px; height: 244px;
    border-width: 8px; font-size: 44px;
  }
  .card--brand .mark {
    left: 278px; top: 39px; width: 362px; height: 362px;
    border-width: 12px; font-size: 66px;
  }

  .divider-stripe {
    position: absolute; left: 0; top: 306px; width: 100%; height: 21px;
    background: var(--paper);
  }
  .info-band {
    position: absolute; left: 0; top: 327px; width: 100%; height: 195px;
    background: var(--teal);
    color: var(--text-dark);
  }
  .identity { position: absolute; left: 60px; top: 50px; }
  .identity__name { font-size: 49px; font-weight: 700; line-height: 1; letter-spacing: 0.3px; }
  .identity__role { font-size: 34px; font-weight: 700; line-height: 1; margin-top: 6px; margin-left: 3px; }

  .band-rule {
    position: absolute; left: 480px; top: 21px; width: 3px; height: 140px;
    background: var(--ink);
  }
  .contacts { position: absolute; left: 497px; top: 34px; list-style: none; }
  .contacts li {
    display: flex; align-items: center;
    height: 43px; font-size: 28px;
  }
  .contacts svg { width: 22px; height: 22px; flex: none; margin-right: 30px; }

  .brand-name {
    position: absolute; left: 0; width: 100%; top: 425px;
    text-align: center; color: var(--paper);
    font-size: 59px; font-weight: 700; letter-spacing: 1px; line-height: 1;
  }
</style>
</head>
<body>
  <section class="card card--info">
    <div class="mark">Varulek</div>
    <div class="divider-stripe"></div>
    <div class="info-band">
      <div class="identity">
        <p class="identity__name">Tom Varulek</p>
        <p class="identity__role">Web Developer</p>
      </div>
      <div class="band-rule"></div>
      <ul class="contacts">
        <li>
          <svg viewBox="0 0 22 22" aria-hidden="true"><rect width="22" height="22" fill="#111"/><path d="M5 9c0-3 12-3 12 0l-3 1-1-2H9L8 10zM7 11h8l1 6H6z" fill="#fff"/></svg>
          570-614-3098
        </li>
        <li>
          <svg viewBox="0 0 22 22" aria-hidden="true"><rect width="22" height="22" fill="#111"/><rect x="4" y="6" width="14" height="10" fill="none" stroke="#fff" stroke-width="1.6"/><path d="M4 6l7 6 7-6" fill="none" stroke="#fff" stroke-width="1.6"/></svg>
          tomvarulek@quillbox.net
        </li>
        <li>
          <svg viewBox="0 0 22 22" aria-hidden="true"><rect width="22" height="22" fill="#111"/><circle cx="11" cy="11" r="7" fill="none" stroke="#fff" stroke-width="1.6"/><path d="M4 11h14M11 4c-4 4-4 10 0 14M11 4c4 4 4 10 0 14" fill="none" stroke="#fff" stroke-width="1.2"/></svg>
          www.tomvarulek.net
        </li>
      </ul>
    </div>
  </section>

  <section class="card card--brand">
    <div class="mark">Varulek</div>
    <p class="brand-name">TOM VARULEK</p>
  </section>
</body>
</html>
```